Business Card for Industrial Distributor

We need a business card design for an industrial distributor. We sell machine parts for the manufacturing and oil industry. We would like the cards to look clean and modern but with a touch of industry.

Our colors are blue/white.

Please feel free to visit our website www.korvelpartsco.com

Target Market(s)

mexican manufacturers in the automobile/aerospace industry

Industry/Entity Type

Industrial

Colors
ffffff
0555a3

```html
<!DOCTYPE html>
<html lang="en">
<head>
<meta charset="UTF-8">
<title>Korvel Business Card</title>
<link href="https://fonts.googleapis.com/css2?family=Montserrat:wght@400;500;700;800&display=swap" rel="stylesheet">
<style>
  :root {
    --stage: #2b2b2d;
    --brand-teal: #075d8c;
    --brand-indigo: #2a3597;
    --ink-blue: #1e5e8c;
    --white: #ffffff;
    --card-w: 680px;
    --card-h: 389px;
  }
  * { box-sizing: border-box; margin: 0; padding: 0; }
  html, body {
    width: 1200px; height: 900px; overflow: hidden;
    background: var(--stage);
    font-family: "Montserrat", sans-serif;
  }
  .stage {
    width: 1200px; height: 900px;
    display: flex; flex-direction: column;
    align-items: center; justify-content: center; gap: 36px;
  }
  .card {
    position: relative;
    width: var(--card-w); height: var(--card-h);
    border-radius: 22px;
    overflow: hidden;
  }
  /* Back side */
  .card-back {
    background: var(--brand-teal);
    color: var(--white);
  }
  .back-mark {
    position: absolute; left: 0; right: 0; top: 110px;
    display: flex; align-items: center; justify-content: center; gap: 18px;
  }
  .back-mark .dot {
    width: 58px; height: 58px; border-radius: 50%;
    background: var(--white);
  }
  .back-mark .wordmark {
    font-weight: 800; font-size: 64px; letter-spacing: 1px;
    color: var(--white);
  }
  .back-url {
    position: absolute; left: 0; right: 0; bottom: 44px;
    text-align: center; font-size: 19px; font-weight: 400; letter-spacing: 0.3px;
  }
  .back-url strong { font-weight: 700; }

  /* Front side */
  .card-front { background: var(--white); }
  .corner-band {
    position: absolute; top: 0; right: 0;
    width: 30px; height: 190px;
    background: var(--brand-indigo);
    border-bottom-left-radius: 30px;
  }
  .front-mark {
    position: absolute; left: 48px; top: 188px;
    display: flex; align-items: center; gap: 12px;
  }
  .front-mark .dot {
    width: 50px; height: 50px; border-radius: 50%;
    background: var(--brand-indigo);
  }
  .front-mark .wordmark {
    font-weight: 800; font-size: 50px; color: var(--brand-indigo);
    letter-spacing: 0.5px;
  }
  .divider {
    position: absolute; left: 318px; top: 120px;
    width: 60px; height: 160px;
  }
  .contact {
    position: absolute; left: 378px; top: 110px;
    color: var(--ink-blue);
  }
  .contact .person {
    font-weight: 700; font-size: 22px; color: var(--brand-indigo);
    letter-spacing: 0.3px;
  }
  .contact .role { font-size: 14px; margin-top: 2px; }
  .contact .address { font-size: 15px; margin-top: 12px; line-height: 1.3; }
  .contact .lines { list-style: none; margin-top: 12px; font-size: 15px; line-height: 1.35; }
  .contact .lines li { display: flex; align-items: center; gap: 10px; }
  .contact .lines svg { width: 11px; height: 11px; flex: none; }
  .contact .lines strong { font-weight: 700; color: var(--brand-indigo); }
</style>
</head>
<body>
<main class="stage">
  <section class="card card-back">
    <div class="back-mark">
      <span class="dot"></span>
      <span class="wordmark">Korvel</span>
    </div>
    <p class="back-url">www.<strong>korvelpartsco</strong>.com</p>
  </section>

  <section class="card card-front">
    <div class="corner-band"></div>
    <div class="front-mark">
      <span class="dot"></span>
      <span class="wordmark">Korvel</span>
    </div>
    <svg class="divider" viewBox="0 0 60 160" aria-hidden="true">
      <line x1="0" y1="0" x2="60" y2="160" stroke="#2a3597" stroke-width="2"/>
    </svg>
    <div class="contact">
      <p class="person">Marlon Pierce</p>
      <p class="role">Director</p>
      <p class="address">P.O. Box 3318<br>Lakeview, MI 49602</p>
      <ul class="lines">
        <li>
          <svg viewBox="0 0 12 12" aria-hidden="true"><path d="M2 1h3l1 3-1.5 1a7 7 0 0 0 2.5 2.5L8 6l3 1v3a1 1 0 0 1-1 1A9 9 0 0 1 1 2a1 1 0 0 1 1-1z" fill="#2a3597"/></svg>
          +330 5180-2294
        </li>
        <li>
          <svg viewBox="0 0 12 12" aria-hidden="true"><rect x="1" y="2.5" width="10" height="7" fill="none" stroke="#2a3597" stroke-width="1.3"/><path d="M1 2.5l5 4 5-4" fill="none" stroke="#2a3597" stroke-width="1.3"/></svg>
          info@korvelpartsco.com
        </li>
        <li>
          <svg viewBox="0 0 12 12" aria-hidden="true"><circle cx="6" cy="6" r="5" fill="none" stroke="#2a3597" stroke-width="1.2"/><path d="M1 6h10M6 1c-2.5 3-2.5 7 0 10M6 1c2.5 3 2.5 7 0 10" fill="none" stroke="#2a3597" stroke-width="1"/></svg>
          <span>www.<strong>korvelpartsco</strong>.com</span>
        </li>
      </ul>
    </div>
  </section>
</main>
</body>
</html>
```